PowerPoint Design for KESTREL Polls

KESTREL Polls stands for 'Kindred Evaluation Scales Tracking Regional Electoral Leanings'. It is a collaborative research effort to format and combine multiple sources of public opinion data from around the world into merged datasets. We need a Microsoft PowerPoint design for our conference/workshop presentations and instructional videos used as part of our research efforts and crowdsourced development. The design should match the website design and logo, which are attached to this contest (these are the files from previous successful design contests).

Slides will contain a lot of data visualizations, tables with statistical output (lots of numbers), and figures. Bullet points will be used frequently on slides and larg blocks of text should be avided. Margins should be narrow to maximize space used and the size of fonts must be large enough (24-32+) to be visible at the back of classrooms and conference rooms.
Updates

I was away at a conference and am now busy with teaching preparation, so I need a few extra days to give adequate feedback.

Target Market(s)

academia, government, non-profits, postgraduates, researchers

Font styles to use
Sans Serif

Colors

Designer to choose colors to be used in the design.

Requirements
Must have
• designs for common slide layouts
Nice to have
• thematic link with website design and logo

```html
<!DOCTYPE html>
<html lang="en">
<head>
<meta charset="utf-8">
<title>KESTREL Polls – Title Slide</title>
<link rel="stylesheet" href="https://fonts.googleapis.com/css2?family=Open+Sans:wght@400;600;700&display=swap">
<style>
  :root {
    --bg: #f1f1f1;
    --brand-blue: #1a77c0;
    --bright-blue: #2a9fe0;
    --muted-text: #555a5f;
    --mark-dot: #2a9fe0;
    --motif-light: rgba(160, 214, 236, 0.9);
    --motif-mid: rgba(143, 190, 224, 0.75);
  }
  * { box-sizing: border-box; margin: 0; padding: 0; }
  html, body {
    width: 1200px;
    height: 900px;
    overflow: hidden;
    background: var(--bg);
  }
  .slide {
    position: relative;
    width: 1200px;
    height: 900px;
    overflow: hidden;
    background: var(--bg);
    font-family: "Open Sans", Arial, sans-serif;
  }
  .motif-area {
    position: absolute;
    left: -420px;
    top: 60px;
    width: 840px;
    height: 780px;
    background:
      radial-gradient(ellipse 50% 50% at 50% 50%,
        var(--motif-light) 0%,
        var(--motif-mid) 35%,
        rgba(143, 190, 224, 0.35) 65%,
        rgba(241, 241, 241, 0) 100%);
  }
  .brand {
    position: absolute;
    right: 48px;
    top: 441px;
    display: flex;
    align-items: center;
    gap: 26px;
  }
  .brand-dot {
    width: 34px;
    height: 34px;
    border-radius: 50%;
    background: var(--mark-dot);
    flex: none;
  }
  .brand-name {
    font-size: 62px;
    font-weight: 600;
    color: var(--brand-blue);
    line-height: 1;
    letter-spacing: -0.5px;
    white-space: nowrap;
  }
  .title-block {
    position: absolute;
    right: 57px;
    top: 583px;
    text-align: right;
  }
  .project-title {
    font-size: 50px;
    font-weight: 700;
    line-height: 1.1;
    color: var(--brand-blue);
    letter-spacing: 0.5px;
    white-space: nowrap;
  }
  .project-title .title-accent {
    color: var(--bright-blue);
    font-weight: 600;
  }
  .project-subtitle {
    margin-top: 20px;
    font-size: 29px;
    font-weight: 400;
    color: var(--muted-text);
    white-space: nowrap;
  }
</style>
</head>
<body>
  <main class="slide">
    <div class="motif-area" role="img" aria-label="Large decorative brand motif in soft light blues"></div>
    <div class="brand">
      <span class="brand-dot" aria-hidden="true"></span>
      <span class="brand-name">KESTREL Polls</span>
    </div>
    <section class="title-block">
      <h1 class="project-title">PROJECT <span class="title-accent">Title Here</span></h1>
      <p class="project-subtitle">Subtext here Subtext here</p>
    </section>
  </main>
</body>
</html>
```